Mortgage Protection Insurance Flyer

The target audience are new home owners so the design needs to be clean and simple.

This a primarily for Final Expense Insurance, but need an area where it says "We Also Specialize In:"
- Medicare Supplement Insurance (MediGap)
- Annuities
- Final Expense

All flyer versions need to be editable. Colors to be used are red, white or black. Refer to my website for colors and photos (corvantshield.com). Will attach my logo and a flyer that I found online that is the format that I am looking for (for 8.5 in. x 11 in version). Need flyer in standard letter size 8.5 in. x11 in. but also in 8.5 in. x 5.5 in and 5.0 in. x 8.0 in. All sizes to be portrait oriented. If picked as winning design, need all flyer versions in full color, also in grey scale and files in all industry file types.

Content can be taken from my website..... corvantshield.com

Do NOT submit if you are not willing to provide all versions as described above for the original project price.

Must use royalty-free stock photos please.

Target Market(s)

New homeowners looking for insurance to protect there mortgage payments

Industry/Entity Type

Life Insurance

Colors
f69fa3

Requirements
Must have
• Colors to be used are red, white or black.
• Need flyer in standard letter size 8.5 in. x11 in. but also in 3.5 in. x 8.5 in (Full Bleed 3.75 in by 8.75 in.) and 4.0 in. x 6.0 in. (Full Bleed 4.12 in x 6.12 in) Each design tailored to the size dimensions (So no squeezing 8.5 x 11 design into a 4.0 x 6.0 space.) All sizes to be portrait oriented. If picked as winning design, need all flyer versions in full color, also in grey scale and files in all file types.
• Do not need physical address on flyer, do need email address on flyer though - tkelwer@corvantshield.com
• So phone number should be prominent, email address and website address should also be contact area.
• If you can not agree to terms above, do not submit any designs.
• Need facebook & twitter logos somewhere in contact info area.
Nice to have
• See sample flyers I have attached.
• White background with red used as primary graphic color and black used as secondary graphic if needed.
• font to be used should similar to one used in logo.

```html
<!DOCTYPE html>
<html lang="en">
<head>
<meta charset="utf-8">
<title>Corvant Shield – Final Expense Rack Card 3.5x8.5</title>
<link href="https://fonts.googleapis.com/css2?family=Oswald:wght@500;700&family=Lato:wght@400;700;900&family=Montserrat:wght@300&display=swap" rel="stylesheet">
<style>
  :root{
    --board:#d9d9d9;
    --ink:#1d1d1d;
    --text:#2b2b2b;
    --white:#ffffff;
    --rule:#d4d4d4;
  }
  *{box-sizing:border-box;margin:0;padding:0}
  html,body{width:1200px;height:1200px;overflow:hidden;background:var(--board)}
  body{position:relative;font-family:'Lato',sans-serif;color:var(--text)}

  .size-label{position:absolute;top:82px;left:0;width:1200px;text-align:center;
    font-family:'Montserrat',sans-serif;font-weight:300;font-size:40px;color:#6a6a6a;letter-spacing:1px}

  .flyer{
    --accent:#e50f14; --accent-dark:#8d1214; --headline-accent:#e50f14; --dot-accent:#e50f14;
    position:absolute;top:202px;width:358px;height:834px;background:var(--white);overflow:hidden}
  .flyer--color{left:178px}
  .flyer--grey{left:665px;
    --accent:#7c7c7c; --accent-dark:#4a4a4a; --headline-accent:#7a7a7a; --dot-accent:#555}

  .hero-photo{position:absolute;left:0;top:0;width:358px;height:270px;
    background:linear-gradient(90deg,#ffffff 0%,#f1f1f1 38%,#d8d2cc 60%,#c9bfb6 80%,#e9e6e2 100%)}
  .flyer--grey .hero-photo{background:linear-gradient(90deg,#ffffff 0%,#f1f1f1 38%,#cfcfcf 60%,#bcbcbc 80%,#e6e6e6 100%)}
  .shape{position:absolute;left:0;top:0}

  .brand{position:absolute;left:28px;top:36px;font-family:'Lato',sans-serif;font-weight:900;
    font-size:15px;letter-spacing:.5px;color:var(--ink)}

  .headline{position:absolute;left:26px;top:128px;font-family:'Oswald',sans-serif;font-weight:700;
    color:var(--ink);line-height:1;text-transform:uppercase}
  .headline span{display:block}
  .headline .l1{font-size:34px}
  .headline .l2{font-size:31px;color:var(--headline-accent);margin-top:2px}
  .headline .l3{font-size:20px;font-weight:500;margin-top:5px;letter-spacing:.2px}

  .benefits{position:absolute;left:171px;top:212px;width:162px;height:216px;
    border-radius:12px;background:linear-gradient(180deg,var(--accent) 0%,var(--accent) 45%,var(--accent-dark) 100%);
    padding:42px 8px 0 10px;color:var(--white)}
  .benefits-tab{position:absolute;left:-6px;top:15px;width:68px;height:13px;border-radius:0 7px 7px 0;
    background:#2e2e2e;color:#fff;font-size:7.5px;font-weight:700;padding:2px 0 0 9px}
  .benefits ul{list-style:none}
  .benefits li{position:relative;padding-left:10px;font-size:7.2px;font-weight:700;line-height:9.4px;margin-bottom:9.6px}
  .tick{position:absolute;left:0;top:1px;width:7px;height:7px}

  .section-title{position:absolute;left:29px;font-weight:900;font-size:11.5px;line-height:12px;color:var(--headline-accent)}
  .intro-title{top:314px}
  .intro{position:absolute;left:29px;top:348px;width:128px;font-size:7.8px;line-height:10.2px;text-align:justify}

  .rates{position:absolute;left:29px;top:446px;width:246px}
  .rate{display:flex;height:11px;margin-bottom:7px}
  .rate-label{width:166px;background:var(--rule);font-size:7px;font-weight:700;padding:1.5px 0 0 5px;color:#333}
  .rate-value{margin-left:3px;width:77px;background:var(--accent);color:#fff;font-size:7px;font-weight:700;text-align:center;padding-top:1.5px}

  .copy{position:absolute;left:29px;width:286px;font-size:7.8px;line-height:10.3px}
  .c1{top:492px}.c2{top:551px}.c3{top:582px}.c4{top:616px}

  .also-title{top:648px}
  .also{position:absolute;left:29px;top:668px;width:290px;font-size:7.8px;list-style:none}
  .also li{position:absolute;padding-left:13px;white-space:nowrap}
  .also .tick{width:8px;height:8px;top:0}
  .also .a1{left:0;top:0}.also .a2{left:0;top:14px}.also .a3{left:197px;top:1px;padding-left:20px}

  .footnote{position:absolute;left:138px;top:695px;width:184px;font-size:5.4px;line-height:7px;color:#333}

  .footer-shape{position:absolute;left:0;top:700px}
  .call{position:absolute;left:24px;top:760px;color:#fff;font-weight:700}
  .call .label{font-size:11px}
  .call .phone{font-size:17.5px;margin-top:2px}
  .contact{position:absolute;left:166px;top:760px;list-style:none;color:#fff;font-size:6.6px;font-weight:700}
  .contact li{display:flex;align-items:center;height:20px;margin-bottom:2px}
  .contact svg{width:19px;height:19px;margin-right:6px}
  .social{position:absolute;left:282px;top:802px;display:flex;gap:2px}
  .social span{width:8px;height:8px;background:#fff;border-radius:1px}
</style>
</head>
<body>
<div class="size-label">3.5x8.5</div>

<!-- Full colour version -->
<article class="flyer flyer--color">
  <div class="hero-photo" role="img" aria-label="Photo of a smiling senior couple embracing"></div>
  <svg class="shape" width="358" height="290" viewBox="0 0 358 290" aria-hidden="true">
    <path d="M0,0 H246 Q170,92 0,102 Z" fill="#fff"/>
    <path d="M0,102 Q170,92 246,0" fill="none" stroke="var(--accent)" stroke-width="4"/>
    <path d="M0,98 Q165,88 238,0" fill="none" stroke="#222" stroke-width="3"/>
    <path d="M0,262 Q180,230 358,238 V290 H0 Z" fill="#fff"/>
    <path d="M0,250 Q180,218 358,226" fill="none" stroke="#222" stroke-width="4"/>
    <path d="M0,258 Q180,228 358,234" fill="none" stroke="var(--accent)" stroke-width="3"/>
  </svg>
  <div class="brand">CORVANT SHIELD</div>
  <h1 class="headline"><span class="l1">Our</span><span class="l2">Plans are</span><span class="l3">Based on yours</span></h1>

  <section class="benefits">
    <div class="benefits-tab">Benefits:</div>
    <ul>
      <li><svg class="tick" viewBox="0 0 10 10"><circle cx="5" cy="5" r="4.3" fill="none" stroke="#fff" stroke-width="1"/><path d="M3,5.2 4.5,6.6 7,3.8" fill="none" stroke="#fff" stroke-width="1"/></svg>All plans we offer are state regulated</li>
      <li><svg class="tick" viewBox="0 0 10 10"><circle cx="5" cy="5" r="4.3" fill="none" stroke="#fff" stroke-width="1"/><path d="M3,5.2 4.5,6.6 7,3.8" fill="none" stroke="#fff" stroke-width="1"/></svg>Relatively low monthly premiums</li>
      <li><svg class="tick" viewBox="0 0 10 10"><circle cx="5" cy="5" r="4.3" fill="none" stroke="#fff" stroke-width="1"/><path d="M3,5.2 4.5,6.6 7,3.8" fill="none" stroke="#fff" stroke-width="1"/></svg>Premiums can never increase</li>
      <li><svg class="tick" viewBox="0 0 10 10"><circle cx="5" cy="5" r="4.3" fill="none" stroke="#fff" stroke-width="1"/><path d="M3,5.2 4.5,6.6 7,3.8" fill="none" stroke="#fff" stroke-width="1"/></svg>Your policy can never be cancelled as long as you pay your premium</li>
      <li><svg class="tick" viewBox="0 0 10 10"><circle cx="5" cy="5" r="4.3" fill="none" stroke="#fff" stroke-width="1"/><path d="M3,5.2 4.5,6.6 7,3.8" fill="none" stroke="#fff" stroke-width="1"/></svg>No medical exams</li>
      <li><svg class="tick" viewBox="0 0 10 10"><circle cx="5" cy="5" r="4.3" fill="none" stroke="#fff" stroke-width="1"/><path d="M3,5.2 4.5,6.6 7,3.8" fill="none" stroke="#fff" stroke-width="1"/></svg>Guaranteed Death Benefit</li>
      <li><svg class="tick" viewBox="0 0 10 10"><circle cx="5" cy="5" r="4.3" fill="none" stroke="#fff" stroke-width="1"/><path d="M3,5.2 4.5,6.6 7,3.8" fill="none" stroke="#fff" stroke-width="1"/></svg>Many policies we offer are Guaranteed Acceptance, "Day 1" coverage, have a child/grandchild rider and/or have an accelerated death benefit rider</li>
    </ul>
  </section>

  <h2 class="section-title intro-title">Final Expense<br>Insurance</h2>
  <p class="intro">Final Expense Insurance is a type of permanent whole life insurance where the death benefit is used to cover (but not limited to) medical costs, funeral costs and other end-of-life expenses. It is a budget friendly option with a death benefit of up to $40k.</p>

  <div class="rates">
    <div class="rate"><div class="rate-label">Monthly premiums as low as</div><div class="rate-value">$11*</div></div>
    <div class="rate"><div class="rate-label">Death Benefits as high as</div><div class="rate-value">$40,000</div></div>
  </div>

  <p class="copy c1">Unforeseen events and a lack of the right kind of insurance can spell trouble quickly. Contact us today, to set up a free assessment time. We will analyze your insurance needs and get you and your family the right coverage quickly at a budget friendly price.</p>
  <p class="copy c2">We have been helping clients in Northern Idaho/Eastern Washington prepare for the unknown.</p>
  <p class="copy c3">We have access to the industry's top insurance carriers so you can get the right coverage, that fits your budget.</p>
  <p class="copy c4">Find out how we can give you the peace of mind of knowing your family will not have a financial burden if something were to happen to you.</p>

  <h2 class="section-title also-title">We Also Specialize In:</h2>
  <ul class="also">
    <li class="a1"><svg class="tick" viewBox="0 0 10 10"><circle cx="5" cy="5" r="4.3" fill="none" stroke="var(--dot-accent)" stroke-width="1"/><path d="M3,5.2 4.5,6.6 7,3.8" fill="none" stroke="var(--dot-accent)" stroke-width="1"/></svg>Medicare Supplement Insurance (Medigap)</li>
    <li class="a2"><svg class="tick" viewBox="0 0 10 10"><circle cx="5" cy="5" r="4.3" fill="none" stroke="var(--dot-accent)" stroke-width="1"/><path d="M3,5.2 4.5,6.6 7,3.8" fill="none" stroke="var(--dot-accent)" stroke-width="1"/></svg>Mortgage Protection Insurance</li>
    <li class="a3"><svg class="tick" viewBox="0 0 10 10"><circle cx="5" cy="5" r="4.3" fill="none" stroke="var(--dot-accent)" stroke-width="1"/><path d="M3,5.2 4.5,6.6 7,3.8" fill="none" stroke="var(--dot-accent)" stroke-width="1"/></svg>Annuities</li>
  </ul>
  <p class="footnote">*Based on an insured that is a 65 year old, non-smoking female<br>that has no medical conditions with a death benefit of $2k</p>

  <svg class="footer-shape" width="358" height="134" viewBox="0 0 358 134" aria-hidden="true">
    <defs><linearGradient id="footColor" x1="0" y1="0" x2="0" y2="1"><stop offset="0" stop-color="#e50f14"/><stop offset="1" stop-color="#7e1416"/></linearGradient></defs>
    <path d="M0,52 Q180,20 358,38 V134 H0 Z" fill="url(#footColor)"/>
    <path d="M0,45 Q180,13 358,31" fill="none" stroke="#222" stroke-width="4"/>
    <path d="M0,36 Q200,20 358,12" fill="none" stroke="#222" stroke-width="2"/>
  </svg>
  <div class="call"><div class="label">Call us now:</div><div class="phone">(208)555.0147</div></div>
  <ul class="contact">
    <li><svg viewBox="0 0 20 20"><circle cx="10" cy="10" r="9" fill="none" stroke="#fff" stroke-width="1.2"/><rect x="5.5" y="7" width="9" height="6.5" fill="none" stroke="#fff"/><path d="M5.5,7 10,11 14.5,7" fill="none" stroke="#fff"/></svg>tkelwer@corvantshield.com</li>
    <li><svg viewBox="0 0 20 20"><circle cx="10" cy="10" r="9" fill="none" stroke="#fff" stroke-width="1.2"/><circle cx="10" cy="10" r="5" fill="none" stroke="#fff"/><path d="M5,10H15M10,5V15M10,5Q6.5,10 10,15M10,5Q13.5,10 10,15" fill="none" stroke="#fff" stroke-width=".8"/></svg>corvantshield.com</li>
  </ul>
  <div class="social"><span></span><span></span></div>
</article>

<!-- Greyscale version -->
<article class="flyer flyer--grey">
  <div class="hero-photo" role="img" aria-label="Greyscale photo of a smiling senior couple embracing"></div>
  <svg class="shape" width="358" height="290" viewBox="0 0 358 290" aria-hidden="true">
    <path d="M0,0 H246 Q170,92 0,102 Z" fill="#fff"/>
    <path d="M0,102 Q170,92 246,0" fill="none" stroke="var(--accent)" stroke-width="4"/>
    <path d="M0,98 Q165,88 238,0" fill="none" stroke="#222" stroke-width="3"/>
    <path d="M0,262 Q180,230 358,238 V290 H0 Z" fill="#fff"/>
    <path d="M0,250 Q180,218 358,226" fill="none" stroke="#222" stroke-width="4"/>
    <path d="M0,258 Q180,228 358,234" fill="none" stroke="var(--accent)" stroke-width="3"/>
  </svg>
  <div class="brand">CORVANT SHIELD</div>
  <h1 class="headline"><span class="l1">Our</span><span class="l2">Plans are</span><span class="l3">Based on yours</span></h1>

  <section class="benefits">
    <div class="benefits-tab">Benefits:</div>
    <ul>
      <li><svg class="tick" viewBox="0 0 10 10"><circle cx="5" cy="5" r="4.3" fill="none" stroke="#fff" stroke-width="1"/><path d="M3,5.2 4.5,6.6 7,3.8" fill="none" stroke="#fff" stroke-width="1"/></svg>All plans we offer are state regulated</li>
      <li><svg class="tick" viewBox="0 0 10 10"><circle cx="5" cy="5" r="4.3" fill="none" stroke="#fff" stroke-width="1"/><path d="M3,5.2 4.5,6.6 7,3.8" fill="none" stroke="#fff" stroke-width="1"/></svg>Relatively low monthly premiums</li>
      <li><svg class="tick" viewBox="0 0 10 10"><circle cx="5" cy="5" r="4.3" fill="none" stroke="#fff" stroke-width="1"/><path d="M3,5.2 4.5,6.6 7,3.8" fill="none" stroke="#fff" stroke-width="1"/></svg>Premiums can never increase</li>
      <li><svg class="tick" viewBox="0 0 10 10"><circle cx="5" cy="5" r="4.3" fill="none" stroke="#fff" stroke-width="1"/><path d="M3,5.2 4.5,6.6 7,3.8" fill="none" stroke="#fff" stroke-width="1"/></svg>Your policy can never be cancelled as long as you pay your premium</li>
      <li><svg class="tick" viewBox="0 0 10 10"><circle cx="5" cy="5" r="4.3" fill="none" stroke="#fff" stroke-width="1"/><path d="M3,5.2 4.5,6.6 7,3.8" fill="none" stroke="#fff" stroke-width="1"/></svg>No medical exams</li>
      <li><svg class="tick" viewBox="0 0 10 10"><circle cx="5" cy="5" r="4.3" fill="none" stroke="#fff" stroke-width="1"/><path d="M3,5.2 4.5,6.6 7,3.8" fill="none" stroke="#fff" stroke-width="1"/></svg>Guaranteed Death Benefit</li>
      <li><svg class="tick" viewBox="0 0 10 10"><circle cx="5" cy="5" r="4.3" fill="none" stroke="#fff" stroke-width="1"/><path d="M3,5.2 4.5,6.6 7,3.8" fill="none" stroke="#fff" stroke-width="1"/></svg>Many policies we offer are Guaranteed Acceptance, "Day 1" coverage, have a child/grandchild rider and/or have an accelerated death benefit rider</li>
    </ul>
  </section>

  <h2 class="section-title intro-title">Final Expense<br>Insurance</h2>
  <p class="intro">Final Expense Insurance is a type of permanent whole life insurance where the death benefit is used to cover (but not limited to) medical costs, funeral costs and other end-of-life expenses. It is a budget friendly option with a death benefit of up to $40k.</p>

  <div class="rates">
    <div class="rate"><div class="rate-label">Monthly premiums as low as</div><div class="rate-value">$11*</div></div>
    <div class="rate"><div class="rate-label">Death Benefits as high as</div><div class="rate-value">$40,000</div></div>
  </div>

  <p class="copy c1">Unforeseen events and a lack of the right kind of insurance can spell trouble quickly. Contact us today, to set up a free assessment time. We will analyze your insurance needs and get you and your family the right coverage quickly at a budget friendly price.</p>
  <p class="copy c2">We have been helping clients in Northern Idaho/Eastern Washington prepare for the unknown.</p>
  <p class="copy c3">We have access to the industry's top insurance carriers so you can get the right coverage, that fits your budget.</p>
  <p class="copy c4">Find out how we can give you the peace of mind of knowing your family will not have a financial burden if something were to happen to you.</p>

  <h2 class="section-title also-title">We Also Specialize In:</h2>
  <ul class="also">
    <li class="a1"><svg class="tick" viewBox="0 0 10 10"><circle cx="5" cy="5" r="4.3" fill="none" stroke="var(--dot-accent)" stroke-width="1"/><path d="M3,5.2 4.5,6.6 7,3.8" fill="none" stroke="var(--dot-accent)" stroke-width="1"/></svg>Medicare Supplement Insurance (Medigap)</li>
    <li class="a2"><svg class="tick" viewBox="0 0 10 10"><circle cx="5" cy="5" r="4.3" fill="none" stroke="var(--dot-accent)" stroke-width="1"/><path d="M3,5.2 4.5,6.6 7,3.8" fill="none" stroke="var(--dot-accent)" stroke-width="1"/></svg>Mortgage Protection Insurance</li>
    <li class="a3"><svg class="tick" viewBox="0 0 10 10"><circle cx="5" cy="5" r="4.3" fill="none" stroke="var(--dot-accent)" stroke-width="1"/><path d="M3,5.2 4.5,6.6 7,3.8" fill="none" stroke="var(--dot-accent)" stroke-width="1"/></svg>Annuities</li>
  </ul>
  <p class="footnote">*Based on an insured that is a 65 year old, non-smoking female<br>that has no medical conditions with a death benefit of $2k</p>

  <svg class="footer-shape" width="358" height="134" viewBox="0 0 358 134" aria-hidden="true">
    <defs><linearGradient id="footGrey" x1="0" y1="0" x2="0" y2="1"><stop offset="0" stop-color="#7c7c7c"/><stop offset="1" stop-color="#3e3e3e"/></linearGradient></defs>
    <path d="M0,52 Q180,20 358,38 V134 H0 Z" fill="url(#footGrey)"/>
    <path d="M0,45 Q180,13 358,31" fill="none" stroke="#222" stroke-width="4"/>
    <path d="M0,36 Q200,20 358,12" fill="none" stroke="#222" stroke-width="2"/>
  </svg>
  <div class="call"><div class="label">Call us now:</div><div class="phone">(208)555.0147</div></div>
  <ul class="contact">
    <li><svg viewBox="0 0 20 20"><circle cx="10" cy="10" r="9" fill="none" stroke="#fff" stroke-width="1.2"/><rect x="5.5" y="7" width="9" height="6.5" fill="none" stroke="#fff"/><path d="M5.5,7 10,11 14.5,7" fill="none" stroke="#fff"/></svg>tkelwer@corvantshield.com</li>
    <li><svg viewBox="0 0 20 20"><circle cx="10" cy="10" r="9" fill="none" stroke="#fff" stroke-width="1.2"/><circle cx="10" cy="10" r="5" fill="none" stroke="#fff"/><path d="M5,10H15M10,5V15M10,5Q6.5,10 10,15M10,5Q13.5,10 10,15" fill="none" stroke="#fff" stroke-width=".8"/></svg>corvantshield.com</li>
  </ul>
  <div class="social"><span></span><span></span></div>
</article>
</body>
</html>
```